Varnik Holdings — Business Card Design Brief
Overview
Design a double-sided business card for Varnik Holdings that highlights our two service arms: Varnik Communications (telecommunications) and Varnik Energy (business energy solutions). The card should feel smart and stand out when handed to clients.

Objectives
Showcase our areas of specialty clearly.
Reflect the overall Varnik / Varnik Holdings brand while acknowledging both arms.
Explore using both logos (Communications + Energy) or one unified logo, depending on the design.

Deliverables
One double-sided business card design (front + back).

Content & Copy
Front (preferred): Logo: Varnik / Varnik Holdings
Descriptor: Business Communications | Business Energy
Back:My contact details and company details
Core products: Business Mobile • Telephony • Internet • Business Energy Solutions

Brand & Visual Direction
We have a group logo currently tailored more toward telecoms, plus a separate Varnik Energy logo.
Please explore layouts that use both logos or just one, whichever works best.
Color: I wouldn't mind seeing an option using our the Blue/Purple gradient from our website (varnik-example.co.uk), but also open to non-gradient approaches and other colours..

Overall look: Smart, modern, and distinctive.
Format & Print Specs
Double-sided business card format. (Use a standard size

Must-Haves
Front: Varnik wording or Varnik Holdings wording with atleast 1 logo also on front “Business Communications | Business Energy.”

Back: Contact + company details and core products.
A design that stands out while remaining professional.

Nice-to-Have Options
A gradient version using our site’s Blue/Purple gradient.
A non-gradient version.
A dual-logo treatment versus a single-logo treatment.

Thanks
Owen

```html
<!DOCTYPE html>
<html lang="en">
<head>
<meta charset="utf-8">
<title>Varnik Holdings — Business Card</title>
<link rel="stylesheet" href="https://fonts.googleapis.com/css2?family=Montserrat:wght@400;500;700;800&display=swap">
<style>
  :root {
    --backdrop: #999999;
    --card-dark: #151515;
    --card-dark-sheen: #3a3a3a;
    --card-light: #ffffff;
    --silver: #c9c9c9;
    --ink: #2b2b2b;
    --ink-strong: #0c0c0c;
    --brand-blue: #3a62c4;
    --accent-blue: #1e9fe0;
    --light-text: #f2f2f2;
  }
  * { box-sizing: border-box; margin: 0; padding: 0; }
  html, body {
    width: 1200px; height: 1108px; overflow: hidden;
    background: var(--backdrop);
    font-family: "Montserrat", sans-serif;
  }
  .card {
    position: absolute; left: 242px;
    width: 715px; height: 409px;
    border-radius: 33px; overflow: hidden;
  }
  /* Front */
  .card-front {
    top: 119px;
    background: linear-gradient(115deg, var(--card-dark) 0%, var(--card-dark) 38%, var(--card-dark-sheen) 52%, #222 66%, var(--card-dark) 100%);
  }
  .front-mark {
    position: absolute; left: 50%; top: 100px;
    width: 136px; height: 136px; margin-left: -68px;
    border-radius: 50%;
    border: 11px solid var(--silver);
  }
  .front-name {
    position: absolute; left: 0; right: 0; top: 236px;
    text-align: center; line-height: 1;
    font-weight: 800; font-size: 78px; letter-spacing: 1px;
    color: var(--silver); text-transform: uppercase;
  }
  .front-services {
    position: absolute; left: 0; right: 0; top: 353px;
    text-align: center; white-space: nowrap;
    font-weight: 500; font-size: 18px; letter-spacing: 0.3px;
    color: var(--light-text);
  }
  /* Back */
  .card-back { top: 580px; background: var(--card-light); }
  .back-mark {
    position: absolute; left: 50%; top: 27px;
    width: 112px; height: 112px; margin-left: -56px;
    border-radius: 50%;
    border: 9px solid var(--brand-blue);
  }
  .back-name {
    position: absolute; left: 0; right: 0; top: 146px;
    text-align: center; color: var(--ink-strong); font-weight: 800;
    text-transform: uppercase; line-height: 1;
  }
  .back-name .word-main { display: block; font-size: 50px; }
  .back-name .word-sub { display: block; font-size: 17px; letter-spacing: 2.6px; margin-top: 6px; }
  .person {
    position: absolute; right: 412px; top: 258px;
    text-align: right; white-space: nowrap;
  }
  .person-name { font-weight: 700; font-size: 33px; color: var(--ink); line-height: 1; }
  .person-role { font-weight: 500; font-size: 19px; color: var(--ink); margin-top: 10px; }
  .divider {
    position: absolute; left: 338px; top: 241px;
    width: 2px; height: 102px; background: var(--accent-blue);
  }
  .contacts {
    position: absolute; left: 372px; top: 234px; list-style: none;
  }
  .contacts li {
    display: flex; align-items: center; height: 28.6px; white-space: nowrap;
    font-weight: 500; font-size: 19px; color: var(--ink);
  }
  .contacts svg { width: 16px; height: 16px; margin-right: 9px; fill: var(--accent-blue); }
  .address {
    position: absolute; left: 0; right: 0; top: 362px;
    text-align: center; font-weight: 500; font-size: 18px; color: var(--ink);
  }
</style>
</head>
<body>
  <section class="card card-front">
    <div class="front-mark"></div>
    <div class="front-name">Varnik</div>
    <p class="front-services">Business Mobile • Telephony • Internet • Business Energy Solutions</p>
  </section>

  <section class="card card-back">
    <div class="back-mark"></div>
    <h1 class="back-name"><span class="word-main">Varnik</span><span class="word-sub">Communications</span></h1>

    <div class="person">
      <p class="person-name">Daniel Hartwell</p>
      <p class="person-role">Managing Director</p>
    </div>
    <div class="divider"></div>

    <ul class="contacts">
      <li>
        <svg viewBox="0 0 16 16" aria-hidden="true"><path d="M3.6 1.2l2.3 2.6-1.3 1.6c.8 1.9 2.2 3.4 4.1 4.3l1.6-1.3 2.6 2.3-1.4 2.2C6.8 12.8 2.9 8.9 1.1 3.8z"/></svg>
        +44 0161 555 0142
      </li>
      <li>
        <svg viewBox="0 0 16 16" aria-hidden="true"><path d="M8 1a7 7 0 0 0-6 10.6L1 15l3.5-1A7 7 0 1 0 8 1zm0 1.5a5.5 5.5 0 1 1-3 10.1l-1.7.5.5-1.6A5.5 5.5 0 0 1 8 2.5z"/></svg>
        +44 7700 900 318 (Live Chat)
      </li>
      <li>
        <svg viewBox="0 0 16 16" aria-hidden="true"><path d="M1 3.5h14v9H1zM1.8 4.3L8 9l6.2-4.7v1.1L8 10.1 1.8 5.4z"/></svg>
        info@varnik-example.co.uk
      </li>
      <li>
        <svg viewBox="0 0 16 16" aria-hidden="true"><path d="M8 1a7 7 0 1 0 0 14A7 7 0 0 0 8 1zm-1 2.3c-.6 1 .4 1.6-.4 2.4-.8.7-2.2.2-2.6 1.3-.3 1 1 1.6 1.8 2.3.8.8-.1 2.2.6 3.4A5.6 5.6 0 0 1 7 3.3zm3.3 9.9c-.2-1.1.6-1.6.2-2.6-.5-1-1.8-.8-2-1.9-.1-1 1.4-1 2.1-1.8.6-.7 0-1.6.5-2.3a5.6 5.6 0 0 1-.8 8.6z"/></svg>
        varnik-example.co.uk
      </li>
    </ul>

    <p class="address">24 Harlow Lane, Leeds, England, LS1 9ZX</p>
  </section>
</body>
</html>
```